Mosquito and outdoor pest management

The uploaded logo must be integrated as the main theme of the card. I would like it to be modern and eye catching. Maybe some backround images or light silver metallic background.
Space enough at the base for contact info to be put in- phone numbers,emails,names,website.
Space on the back for short blog and lines for hand writing..calling card.
Commercial- golf courses, schools, outdoor function properties, pre event treatments.
Residential- retirement villages, townhome complexes and general houses
Management

```html
<!DOCTYPE html>
<html lang="en">
<head>
<meta charset="utf-8">
<title>Ridgeway Mosquito – Business Card</title>
<link rel="stylesheet" href="https://fonts.googleapis.com/css2?family=Lato:wght@400;700;900&display=swap">
<style>
  :root {
    --stage: #3a3a3c;
    --card: #ffffff;
    --card-shade: #eeeeee;
    --brand-red: #d61f2c;
    --brand-red-dark: #b3141f;
    --ink: #1f1f1f;
    --ink-soft: #3c3c3c;
    --rule: #d9d9d9;
    --wash-pink: #f29aa2;
  }
  * { box-sizing: border-box; margin: 0; padding: 0; }
  html, body { width: 1200px; height: 997px; overflow: hidden; }
  body {
    background: var(--stage);
    font-family: 'Lato', Arial, sans-serif;
    position: relative;
  }
  .card {
    position: absolute;
    width: 720px;
    height: 412px;
    border-radius: 22px;
    background: linear-gradient(160deg, var(--card) 55%, var(--card-shade));
    overflow: hidden;
    box-shadow: 0 14px 30px rgba(0,0,0,.45);
  }
  .card--back { left: 90px; top: 50px; }
  .card--front { left: 390px; top: 520px; }

  /* Shared wordmark */
  .wordmark {
    position: absolute;
    display: flex;
    align-items: center;
    gap: 10px;
    font-weight: 900;
    color: var(--ink);
    letter-spacing: .5px;
  }
  .wordmark__dot {
    width: 14px; height: 14px;
    background: var(--brand-red);
  }

  /* Back */
  .back__illustration {
    position: absolute;
    left: -20px; top: 120px;
    width: 420px; height: 320px;
    background: radial-gradient(ellipse at 40% 55%, var(--wash-pink) 0%, rgba(242,154,162,.55) 45%, rgba(242,154,162,0) 72%);
  }
  .card--back .wordmark { left: 330px; top: 52px; font-size: 26px; }
  .writing-lines { position: absolute; left: 300px; top: 125px; width: 380px; }
  .writing-lines span {
    display: block;
    height: 1px;
    background: var(--rule);
    margin-bottom: 46px;
  }

  /* Front */
  .card--front .wordmark { left: 50px; top: 170px; font-size: 28px; }
  .front__divider {
    position: absolute;
    left: 388px; top: 70px;
    width: 3px; height: 150px;
    background: linear-gradient(to bottom, rgba(214,31,44,0), var(--brand-red) 35%, rgba(214,31,44,0));
  }
  .contact { position: absolute; left: 420px; top: 62px; width: 280px; }
  .contact__name { font-size: 25px; font-weight: 900; color: var(--brand-red); }
  .contact__title { font-size: 14px; font-weight: 700; color: var(--ink); margin-bottom: 24px; }
  .contact__list { list-style: none; }
  .contact__item {
    display: flex; align-items: flex-start; gap: 10px;
    font-size: 13px; line-height: 20px; color: var(--ink-soft);
    margin-bottom: 6px;
  }
  .contact__icon {
    flex: 0 0 20px; width: 20px; height: 20px;
    border-radius: 5px;
    background: var(--brand-red);
    display: flex; align-items: center; justify-content: center;
  }
  .front__band-rule {
    position: absolute; left: 0; right: 0; height: 2px;
    background: var(--brand-red);
  }
  .front__band-rule--top { top: 282px; }
  .front__band-rule--bottom { top: 358px; }
  .front__band {
    position: absolute; left: 0; right: 0; top: 290px; height: 62px;
    background: linear-gradient(to bottom, var(--brand-red), var(--brand-red-dark));
    display: flex; align-items: center; justify-content: center;
  }
  .front__website {
    color: #fff; font-size: 20px; letter-spacing: 3px;
  }
</style>
</head>
<body>

  <section class="card card--back" aria-label="Card back">
    <div class="back__illustration" role="img" aria-label="Large faded mosquito illustration"></div>
    <div class="wordmark"><span class="wordmark__dot"></span>Ridgeway Mosquito</div>
    <div class="writing-lines">
      <span></span><span></span><span></span><span></span><span></span><span></span>
    </div>
  </section>

  <section class="card card--front" aria-label="Card front">
    <div class="wordmark"><span class="wordmark__dot"></span>Ridgeway Mosquito</div>
    <div class="front__divider"></div>
    <div class="contact">
      <p class="contact__name">Liam Hartwell</p>
      <p class="contact__title">Creative Director</p>
      <ul class="contact__list">
        <li class="contact__item">
          <span class="contact__icon">
            <svg width="12" height="12" viewBox="0 0 24 24"><path fill="#fff" d="M6.6 10.8a15 15 0 0 0 6.6 6.6l2.2-2.2c.3-.3.7-.4 1-.2 1.1.4 2.3.6 3.6.6.6 0 1 .4 1 1V20c0 .6-.4 1-1 1A17 17 0 0 1 3 4c0-.6.4-1 1-1h3.5c.6 0 1 .4 1 1 0 1.3.2 2.5.6 3.6.1.3 0 .7-.2 1z"/></svg>
          </span>
          +44- 700-123-456
        </li>
        <li class="contact__item">
          <span class="contact__icon">
            <svg width="12" height="10" viewBox="0 0 24 18"><rect x="1" y="1" width="22" height="16" rx="2" fill="none" stroke="#fff" stroke-width="2.4"/><path d="M2 2l10 8 10-8" fill="none" stroke="#fff" stroke-width="2.4"/></svg>
          </span>
          liam@rmopc.com
        </li>
        <li class="contact__item">
          <span class="contact__icon">
            <svg width="10" height="13" viewBox="0 0 20 26"><path fill="#fff" d="M10 0a10 10 0 0 0-10 10c0 7.5 10 16 10 16s10-8.5 10-16A10 10 0 0 0 10 0zm0 14a4 4 0 1 1 0-8 4 4 0 0 1 0 8z"/></svg>
          </span>
          #8, Elm Grove, Harbour View Street, Northfield, N12 3AB
        </li>
      </ul>
    </div>
    <div class="front__band-rule front__band-rule--top"></div>
    <div class="front__band"><span class="front__website">www.rmopc.com</span></div>
    <div class="front__band-rule front__band-rule--bottom"></div>
  </section>

</body>
</html>
```